Build Website for Moss Quay Studio that helps content creators build businesses

Please help me create a website for my company that helps content creators build businesses around their audience. I have attached a design and vibe that I am going for at mossquay.io.

Open for changes, but I want to keep the colour I currently have (a light teal). Ultimately the brand is playful but should come off as a very modern elevated brand.

I am looking for a few pages including

1. Home (with clear CTA button)
A section where I can input what the company does, and some brands that we have launched

2. About Me
A simple page, that has preferably able to put a circular image of myself and then give a quick background about the company

3. Blog (can you include how blog posts will appear and it should sit nicely in the page)
This ideally is a section that will be able to link to another software so my blogs automatically flow into here or posts. But otherwise it should have sections of blocks where creators can see about topics that I post about

4. Contact (this should include a form that will allow users to contact me)
Finally a contact page where it links my socials, similar what is there, but ideally there is a form they can fill out which I can link to my inbox as well. This should be a simple page as well

Create a multi page website, including a page that will link or can link blog post

Similar to this vibe and logo - https://mossquay.io/

Target Market(s)

Content Creators

Coding

Coded - Design and coding required

Number of Pages Required

4 page

Requirements
Must have
• Home, Contact Me (Including a place to submit an enquiry and form), Blog Post Page As well

```html
<!DOCTYPE html>
<html lang="en">
<head>
<meta charset="utf-8">
<title>Moss Quay — Building Businesses</title>
<link rel="stylesheet" href="https://fonts.googleapis.com/css2?family=Plus+Jakarta+Sans:wght@300;400;500;600;700;800&display=swap">
<style>
:root{
  --ink:#2f4f5a;
  --heading:#3a6171;
  --deep:#33545f;
  --teal:#a9d9df;
  --teal-soft:#cdeef1;
  --mist:#e8fbfb;
  --text:#3d4a50;
  --white:#ffffff;
}
*{margin:0;padding:0;box-sizing:border-box}
html,body{width:1200px;height:3134px;overflow:hidden}
body{position:relative;font-family:"Plus Jakarta Sans",sans-serif;color:var(--text);
  background:radial-gradient(ellipse 400px 500px at 0 500px,#e4f4f7 0,rgba(255,255,255,0) 100%),
             radial-gradient(ellipse 350px 350px at 1200px 60px,#e4f4f7 0,rgba(255,255,255,0) 100%),#fff}
.abs{position:absolute}
.backdrop{position:absolute;left:0;top:0}
.brand-mark{position:absolute;border-radius:40px;background:linear-gradient(160deg,#d7f0f3,var(--teal))}
.brand-name{position:absolute;font-weight:400;letter-spacing:3px;color:var(--deep);white-space:nowrap}
.nav a{position:absolute;top:52px;font-size:14.5px;color:var(--deep);text-decoration:none;font-weight:500}
.nav .active{left:572px;top:45px;width:77px;height:30px;border:1.5px solid var(--ink);border-radius:16px;background:#d9eff2;text-align:center;line-height:27px}
.social{position:absolute;width:32px;height:32px;border:1.5px solid var(--ink);border-radius:50%;display:flex;align-items:center;justify-content:center}
.social::after{content:"";width:8px;height:8px;border-radius:50%;background:var(--ink)}
.hero-title{left:129px;top:228px;font-size:51px;line-height:57px;font-weight:800;color:var(--heading);letter-spacing:.5px}
.hero-sub{left:132px;top:362px;font-size:24px;line-height:38px;font-weight:300;color:var(--ink)}
.btn{position:absolute;background:var(--deep);color:#fff;font-weight:700;border-radius:22px;display:flex;align-items:center;justify-content:center;text-decoration:none}
.btn-lg{font-size:16px}
.btn-sm{font-size:10px;border-radius:12px}
.art{position:absolute;background:linear-gradient(150deg,#f2fafb,var(--teal-soft) 60%,var(--teal));border-radius:18px}
.section-title{position:absolute;left:0;width:1200px;text-align:center;font-size:30px;font-weight:700;color:var(--heading)}
.dash{position:absolute;height:2px;width:36px;background:var(--deep)}
.lead{position:absolute;left:0;width:1200px;text-align:center;font-size:16.5px;line-height:24px;font-weight:300;color:var(--ink)}
.service{position:absolute;width:222px;height:234px;background:#fff;border-radius:18px;box-shadow:0 8px 28px rgba(60,110,120,.08);text-align:center}
.service svg{display:block;margin:0 auto}
.service h3{font-size:14.5px;font-weight:500;color:#1f2f35;margin-top:18px}
.service p{font-size:12.5px;line-height:18px;font-weight:300;margin:10px 22px 0;color:#2d3a40}
.photo{left:144px;top:1240px;width:417px;height:437px;border-radius:24px;background:linear-gradient(180deg,#c9d3d6,#9eb0b8 45%,#4b6074)}
.float-card{position:absolute;background:#fff;border-radius:10px;box-shadow:0 6px 20px rgba(40,80,90,.1);display:flex;gap:10px;align-items:center;padding:0 12px}
.float-card .ic{width:20px;height:20px;border:1.5px solid var(--ink);border-radius:50%;flex:none}
.float-card b{display:block;font-size:10.5px;font-weight:500;color:#1f2f35}
.float-card span{display:block;font-size:9.5px;line-height:13px;font-weight:300}
.about-copy{left:663px;top:1380px;width:410px;font-size:16px;line-height:24px;font-weight:300;color:#2d3a40}
.post{position:absolute;top:1947px;width:294px;height:430px;background:#fff;border-radius:14px;box-shadow:0 8px 28px rgba(60,110,120,.08)}
.post .thumb{position:absolute;left:13px;top:16px;width:268px;height:188px;border-radius:12px}
.post h4{position:absolute;left:34px;top:232px;width:240px;font-size:15.5px;line-height:21px;font-weight:500;color:#1f2f35}
.post p{position:absolute;left:34px;top:290px;width:230px;font-size:11.3px;line-height:16px;font-weight:300}
.arrow{position:absolute;width:34px;height:34px;border:1.5px solid var(--ink);border-radius:50%;background:#fff}
.arrow svg{position:absolute;left:9px;top:9px}
.partner{position:absolute;top:2572px;width:176px;height:95px;background:#fff;border-radius:10px;box-shadow:0 6px 20px rgba(60,110,120,.08);display:flex;align-items:center;justify-content:center;font-size:15px;font-weight:700;letter-spacing:2px;color:#1f2f35;text-transform:uppercase}
.foot-nav a{position:absolute;top:2957px;font-size:14.5px;color:var(--deep);text-decoration:none;transform:translateX(-50%)}
.rule{position:absolute;top:3022px;height:1px;width:45px;background:var(--ink)}
</style>
</head>
<body>

<svg class="backdrop" width="1200" height="3134" aria-hidden="true">
  <path d="M0 1230 C150 1120 300 1040 600 1020 C900 1000 1080 1120 1200 1200 L1200 1765 L0 1765 Z" fill="#e3f8f9"/>
  <path d="M0 2300 C200 2260 400 2250 600 2250 C850 2250 1050 2270 1200 2300 L1200 2727 L0 2727 Z" fill="#e8fbfb"/>
</svg>

<header>
  <div class="brand-mark" role="img" aria-label="Moss Quay mascot illustration" style="left:150px;top:30px;width:135px;height:88px"></div>
  <div class="brand-name" style="left:130px;top:122px;font-size:23px">MOSS QUAY</div>
  <nav class="nav">
    <a class="active" href="https://mossquay.io/">HOME</a>
    <a href="https://mossquay.io/" style="left:675px">ABOUT ME</a>
    <a href="https://mossquay.io/" style="left:780px">BLOG</a>
    <a href="https://mossquay.io/" style="left:852px">CONTACT</a>
  </nav>
  <span class="social" style="left:955px;top:44px"></span>
  <span class="social" style="left:994px;top:44px"></span>
  <span class="social" style="left:1035px;top:44px"></span>
</header>

<section class="hero">
  <h1 class="abs hero-title">BUILDING<br>BUSINESSES</h1>
  <p class="abs hero-sub">Helping Content Creators<br>Build Successful Brands</p>
  <a class="btn btn-lg" href="https://mossquay.io/" style="left:133px;top:466px;width:152px;height:44px">GET STARTED</a>
  <div class="art" role="img" aria-label="Illustration of a content creator with a laptop surrounded by video players and plants" style="left:481px;top:140px;width:614px;height:453px"></div>
</section>

<section class="services">
  <h2 class="section-title" style="top:656px">WHAT WE DO</h2>
  <p class="lead" style="top:715px">At Moss Quay Studio, we offer a range of services to support content creators in<br>building and growing their brands. Our services include:</p>
  <span class="dash" style="left:582px;top:799px"></span>

  <article class="service" style="left:120px;top:919px">
    <svg width="52" height="48" style="margin-top:40px" fill="none" stroke="#2f4f5a" stroke-width="2"><rect x="3" y="3" width="46" height="32" rx="2"/><path d="M18 35v8h16v-8M12 44h28M10 28h8M22 28v-8M28 28v-12M34 28v-6"/></svg>
    <h3>BRAND STRATEGY</h3>
    <p>Crafting unique brand identities and strategies</p>
  </article>
  <article class="service" style="left:369px;top:863px">
    <svg width="50" height="50" style="margin-top:38px" fill="none" stroke="#2f4f5a" stroke-width="2"><rect x="4" y="3" width="42" height="44" rx="2"/><path d="M11 12h28M11 20h14M11 28h20M11 36h16M30 38l12-14"/></svg>
    <h3>CONTENT CREATION</h3>
    <p>Providing tools and guidance for creating high-quality content</p>
  </article>
  <article class="service" style="left:613px;top:916px">
    <svg width="54" height="50" style="margin-top:38px" fill="none" stroke="#2f4f5a" stroke-width="2"><rect x="3" y="18" width="30" height="24" rx="2"/><circle cx="42" cy="12" r="8"/><path d="M8 42v6h36v-6M10 26h14M10 33h10"/></svg>
    <h3>MARKETING &amp; PROMOTION</h3>
    <p>Developing effective marketing campaigns to reach your audience.</p>
  </article>
  <article class="service" style="left:860px;top:947px">
    <svg width="50" height="50" style="margin-top:40px" fill="none" stroke="#2f4f5a" stroke-width="2"><rect x="12" y="3" width="26" height="36" rx="2"/><circle cx="25" cy="24" r="6"/><path d="M4 40h42v6H4zM17 11h16"/></svg>
    <h3>MONETIZATION</h3>
    <p>Helping you turn your passion into profit.</p>
  </article>
</section>

<section class="about">
  <div class="abs photo" role="img" aria-label="Portrait photo of the founder in a blue blazer, arms crossed, in a bright office"></div>
  <div class="float-card" style="left:83px;top:1330px;width:176px;height:67px"><i class="ic"></i><div><b>LOREM IPSUM</b><span>Sed ut perspiciatis unde omnis iste natus .</span></div></div>
  <div class="float-card" style="left:436px;top:1458px;width:175px;height:68px"><i class="ic"></i><div><b>LOREM IPSUM</b><span>Sed ut perspiciatis unde omnis iste natus .</span></div></div>
  <div class="float-card" style="left:251px;top:1647px;width:191px;height:69px"><i class="ic"></i><div><b>LOREM IPSUM</b><span>Sed ut perspiciatis unde omnis iste natus .</span></div></div>

  <h2 class="abs" style="left:663px;top:1274px;font-size:30px;font-weight:700;color:var(--heading)">ABOUT ME</h2>
  <span class="dash" style="left:663px;top:1338px"></span>
  <p class="abs about-copy">Sed ut perspiciatis unde omnis iste natus error sit volupt atem accusantium doloremque laudantium, totam rem aperiam, eaque ipsa quae ab illo inventore veritatis et quasi architecto beatae vitae dicta sunt explicabo. Nemo enim ipsam voluptatem quia voluptas sit aspernatur aut odit aut fugit, sed quia consequuntur magni dolores eos qui ratione voluptatem sequi nesciunt. Neque porro quisquam est.</p>
  <a class="btn btn-lg" href="https://mossquay.io/" style="left:663px;top:1609px;width:139px;height:44px">READ MORE</a>
  <div class="brand-mark" role="img" aria-label="Mascot illustration sitting on an ice floe" style="left:931px;top:1612px;width:269px;height:153px;border-radius:120px 120px 0 0"></div>
</section>

<section class="blog">
  <h2 class="section-title" style="top:1826px">LATEST BLOG</h2>
  <span class="dash" style="left:585px;top:1895px"></span>
  <a class="arrow" href="https://mossquay.io/" style="left:52px;top:2133px"><svg width="14" height="14" fill="none" stroke="#2f4f5a" stroke-width="1.6"><path d="M9 2L4 7l5 5"/></svg></a>
  <a class="arrow" href="https://mossquay.io/" style="left:1109px;top:2133px"><svg width="14" height="14" fill="none" stroke="#2f4f5a" stroke-width="1.6"><path d="M5 2l5 5-5 5"/></svg></a>

  <article class="post" style="left:131px">
    <div class="thumb" role="img" aria-label="Photo of a person working on a laptop at a wooden desk" style="background:linear-gradient(135deg,#6b4a36,#a0603f 50%,#c2452f)"></div>
    <h4>Lorem ipsum dolor sit amet, consectetur adipiscin.</h4>
    <p>Sed ut perspiciatis unde omnis iste natus error sit volupt atem accusantium dolor emque laudantium, totam rem aperiam, eaque ipsa quae ab illo.</p>
    <a class="btn btn-sm" href="https://mossquay.io/" style="left:33px;top:360px;width:89px;height:28px">READ MORE</a>
  </article>
  <article class="post" style="left:454px">
    <div class="thumb" role="img" aria-label="Photo of three colleagues talking in a glass office" style="background:linear-gradient(135deg,#dfe3e6,#9aa3aa 55%,#3b3f47)"></div>
    <h4>Lorem ipsum dolor sit amet, consectetur adipiscin.</h4>
    <p>Sed ut perspiciatis unde omnis iste natus error sit volupt atem accusantium dolor emque laudantium, totam rem aperiam, eaque ipsa quae ab illo.</p>
    <a class="btn btn-sm" href="https://mossquay.io/" style="left:33px;top:360px;width:89px;height:28px">READ MORE</a>
  </article>
  <article class="post" style="left:776px">
    <div class="thumb" role="img" aria-label="Photo of hands editing video on a laptop in a dim room" style="background:linear-gradient(135deg,#2a3d55,#1b3f5e 50%,#5b8fa8)"></div>
    <h4>Lorem ipsum dolor sit amet, consectetur adipiscin.</h4>
    <p>Sed ut perspiciatis unde omnis iste natus error sit volupt atem accusantium dolor emque laudantium, totam rem aperiam, eaque ipsa quae ab illo.</p>
    <a class="btn btn-sm" href="https://mossquay.io/" style="left:33px;top:360px;width:89px;height:28px">READ MORE</a>
  </article>
</section>

<section class="brands">
  <h2 class="section-title" style="top:2448px">BRANDS WE'VE LAUNCHED</h2>
  <span class="dash" style="left:585px;top:2516px"></span>
  <a class="arrow" href="https://mossquay.io/" style="left:66px;top:2602px"><svg width="14" height="14" fill="none" stroke="#2f4f5a" stroke-width="1.6"><path d="M9 2L4 7l5 5"/></svg></a>
  <a class="arrow" href="https://mossquay.io/" style="left:1100px;top:2602px"><svg width="14" height="14" fill="none" stroke="#2f4f5a" stroke-width="1.6"><path d="M5 2l5 5-5 5"/></svg></a>
  <div class="partner" style="left:134px">Maison Orel</div>
  <div class="partner" style="left:324px">Vantesse</div>
  <div class="partner" style="left:514px">Giraud</div>
  <div class="partner" style="left:703px">Quattra</div>
  <div class="partner" style="left:893px;font-size:13px;letter-spacing:1px">Dellino &amp; Gray</div>
</section>

<footer>
  <div class="brand-mark" role="img" aria-label="Moss Quay mascot illustration" style="left:521px;top:2779px;width:161px;height:93px"></div>
  <div class="brand-name" style="left:0;width:1200px;text-align:center;top:2889px;font-size:29px">MOSS QUAY</div>
  <nav class="foot-nav">
    <a href="https://mossquay.io/" style="left:455px">HOME</a>
    <a href="https://mossquay.io/" style="left:555px">ABOUT ME</a>
    <a href="https://mossquay.io/" style="left:644px">BLOG</a>
    <a href="https://mossquay.io/" style="left:730px">CONTACT</a>
  </nav>
  <span class="rule" style="left:436px"></span>
  <span class="abs" style="left:496px;top:3013px;font-size:14px;color:var(--deep)">FOLLOW ME</span>
  <span class="social" style="left:588px;top:3006px"></span>
  <span class="social" style="left:628px;top:3006px"></span>
  <span class="social" style="left:669px;top:3006px"></span>
  <span class="rule" style="left:716px"></span>
  <p class="abs" style="left:0;width:1200px;text-align:center;top:3068px;font-size:12.5px;color:var(--deep)">Copyright © 2024 All Rights Reserved</p>
</footer>

</body>
</html>
```